Charity Initiative needs a WebPage design

We need a web design for charity initiative by two young guys riding their bikes around Australia to support HarbourLight which helps people with depression and anxiety. Full brief and requirements are attached in the PDF and word document. We have the logo already done and attached. Website will be done in Wordpress and need to get Donations, display current donations, show live Video feed, GPS tracker, Blogs etc and also ability to sell merchandise later

Target Market(s)

Sponsors, Business, Young People

Number of Pages Required

4 page

Font styles to use
Serif
Sans Serif
Decorative
Script

Requirements
Must have
• As per Brief and also Donation status etc
Nice to have
• Please check my logo and read the Bried

```html
<!DOCTYPE html>
<html lang="en">
<head>
<meta charset="utf-8">
<title>Southern Loop Ride</title>
<link href="https://fonts.googleapis.com/css2?family=Oswald:wght@400;500&family=Roboto:wght@300;400;500;700&display=swap" rel="stylesheet">
<style>
:root{
  --pink:#e8175d;
  --teal:#3fb0a8;
  --teal-dark:#2f9a92;
  --ink:#333;
  --muted:#8a8a8a;
  --panel:#ffffff;
  --band:#f1f1f1;
  --btn:#444;
}
*{box-sizing:border-box;margin:0;padding:0}
html,body{width:1200px;height:2476px;overflow:hidden}
body{position:relative;font-family:'Roboto',sans-serif;color:var(--ink);
  background:linear-gradient(180deg,#b9d6d8 0%,#cfe3e0 30%,#a9c7b5 60%,#c4d6b8 85%,#b8cfb0 100%)}
.abs{position:absolute}
.page{left:99px;top:40px;width:1002px;height:2358px;background:var(--panel);border-top:5px solid var(--teal)}
.logo{left:0;width:1200px;top:88px;text-align:center;font-family:'Roboto',sans-serif;font-weight:700;font-size:36px;color:var(--pink);letter-spacing:1px}
.logo .dot{display:inline-block;width:24px;height:24px;background:var(--pink);border-radius:50%;margin-right:12px;vertical-align:-3px}
.nav{left:120px;top:180px;width:959px;height:59px;background:var(--pink);display:flex;align-items:center;font-size:13px;color:#fff;text-transform:uppercase;font-weight:500}
.nav a{color:#fff;text-decoration:none;display:flex;align-items:center;justify-content:center;height:100%}
.nav .home{background:var(--teal);width:94px}
.nav .item{width:112px}
.nav .donate{margin-left:auto;margin-right:21px;background:var(--btn);height:37px;padding:0 16px;border-radius:2px}
.slider{left:120px;top:264px;width:959px;height:474px;border:1px solid #ddd;padding:4px;background:#fff}
.slider .photo{width:100%;height:100%;background:linear-gradient(180deg,#2f4a6a 0%,#d9a24a 32%,#5b6f86 45%,#8f949a 65%,#6c6f73 100%)}
.dots{left:0;width:1200px;top:714px;display:flex;justify-content:center;gap:12px}
.dots span{width:10px;height:10px;border-radius:50%;background:#fff}
.dots span.on{background:var(--teal)}
.band{left:99px;top:738px;width:1002px;height:354px;background:var(--band)}
.video{left:120px;top:766px;width:479px;height:292px;background:linear-gradient(180deg,#55606a 0%,#7b7f83 50%,#5d5a55 100%)}
.play{left:325px;top:886px;width:70px;height:48px;background:#e02020;border-radius:12px}
.play svg{display:block;margin:12px auto 0}
.welcome-title{left:622px;top:762px;font-family:'Oswald',sans-serif;font-weight:400;font-size:28px;color:var(--pink);text-transform:uppercase}
.welcome-text{left:622px;top:812px;width:458px;font-size:11.5px;line-height:21px;color:var(--muted);text-align:justify}
.h-section{font-family:'Oswald',sans-serif;font-weight:400;font-size:28px;color:var(--pink);text-transform:uppercase}
.post-img{left:120px;width:585px;height:235px;border-radius:8px}
.post-img.one{top:1176px;background:linear-gradient(180deg,#c9a56c 0%,#e3c79a 40%,#6b5a45 75%,#3a342c 100%)}
.post-img.two{top:1637px;background:linear-gradient(180deg,#8fa96a 0%,#6f9a3c 40%,#5c8a2e 70%,#86a05a 100%)}
.post-title{left:120px;font-size:19px;color:var(--ink)}
.post-date{left:120px;font-size:13px;color:var(--pink)}
.post-text{left:120px;width:585px;font-size:11.5px;line-height:19px;color:var(--muted)}
.meta{left:120px;width:585px;height:37px;border-top:1px solid var(--teal);border-bottom:1px solid var(--teal);display:flex;align-items:center;font-size:11px;color:var(--muted);gap:28px;padding-left:2px}
.meta b{color:var(--teal);font-weight:400}
.meta .ico{display:inline-flex;align-items:center;gap:8px}
.meta .share{margin-left:auto;display:flex;gap:9px;padding-right:10px}
.meta .share span{width:21px;height:21px;border:1px solid var(--teal);border-radius:50%}
.pager{left:120px;width:585px;top:2090px;display:flex;justify-content:center;gap:18px;font-size:13px;align-items:center}
.pager span{width:24px;height:24px;display:flex;align-items:center;justify-content:center}
.pager .on{background:var(--pink);color:#fff}
.pager .arr{color:var(--teal)}
.don{left:733px;top:1119px;width:346px;height:241px;border:1px solid #ddd;background:#fff}
.don-head{height:62px;background:var(--pink);color:#fff;font-family:'Oswald',sans-serif;font-size:27px;display:flex;align-items:center;justify-content:center;text-transform:uppercase}
.don-row{display:flex;justify-content:space-between;padding:24px 10px 0 12px;font-size:19px;font-weight:500;color:#555}
.don-row small{display:block;font-size:14px;font-weight:400;color:var(--muted);margin-top:4px}
.don-row .r{text-align:right}
.bar{margin:20px 9px 0 12px;height:11px;border-radius:6px;background:#e4e4e4;overflow:hidden}
.bar i{display:block;width:47%;height:100%;background:var(--teal)}
.don-stats{display:flex;justify-content:space-around;padding:14px 8px 0;font-size:13px;font-weight:500;color:#444;text-align:center}
.don-stats small{display:block;font-size:11px;font-weight:400;color:var(--muted);margin-top:3px}
.gps{left:733px;top:1394px;width:346px;height:533px;border:1px solid #ddd;background:#fff}
.gps-head{height:88px;background:var(--teal);color:#fff;text-align:center;position:relative}
.gps-head h3{font-family:'Oswald',sans-serif;font-weight:400;font-size:27px;padding-top:14px;text-transform:uppercase}
.gps-head p{font-size:14px;margin-top:2px}
.gps-head .wd{position:absolute;left:10px;top:10px;display:flex;gap:4px}
.gps-head .wd span{width:7px;height:7px;border-radius:50%;background:#fff}
.gps-head .wd span:first-child{background:var(--pink)}
.gps-head .bat{position:absolute;right:34px;top:10px;width:22px;height:10px;border:1px solid #fff;padding:1px}
.gps-head .bat i{display:block;height:100%;background:#7fe08a}
.gps-head .wifi{position:absolute;right:10px;top:7px}
.feed{height:102px;display:flex;align-items:center;padding:0 12px;gap:20px;border-bottom:1px solid #eee}
.feed .avatar{width:58px;height:58px;background:#000}
.feed h4{font-weight:400;font-size:16px;color:#444}
.feed p{font-size:11px;color:var(--muted);margin-top:6px}
.pace{height:111px;background:var(--pink);color:#fff;display:flex}
.pace div{flex:1;text-align:center;padding-top:18px;font-size:19px;font-weight:500}
.pace div+div{border-left:1px solid rgba(255,255,255,.5)}
.pace strong{display:block;font-family:'Oswald',sans-serif;font-weight:400;font-size:38px;line-height:48px}
.pace strong small{font-size:20px}
.map{height:231px;background:linear-gradient(180deg,#bcd9ee 0%,#e9dca8 35%,#e2c98c 65%,#bcd9ee 100%)}
.side-title{left:733px;top:1963px;font-size:17px;font-weight:500;color:var(--ink)}
.side-text{left:733px;top:2001px;width:346px;font-size:11.5px;line-height:19px;color:var(--muted);text-align:justify}
.side-text a{color:var(--pink)}
.read{left:733px;width:346px;top:2092px;text-align:right;font-size:11px;color:var(--teal);text-decoration:underline;font-style:italic}
.footer{left:99px;top:2135px;width:1002px;height:263px;background:var(--teal);color:#fff}
.f-col{position:absolute;top:38px}
.f-col h5{font-size:14px;font-weight:500;text-transform:uppercase;margin-bottom:14px}
.f-col p{font-size:11px;line-height:19px}
.f-line{display:flex;align-items:center;gap:14px;margin-top:8px}
.f-line .big{font-size:17px}
.news{display:flex;margin-top:20px}
.news span{width:168px;height:37px;background:#fff;color:#333;font-size:10px;display:flex;align-items:center;padding-left:14px}
.news b{width:80px;height:37px;background:var(--pink);font-weight:400;font-size:14px;display:flex;align-items:center;justify-content:center}
.soc{display:flex;gap:18px;margin-top:6px}
.soc span{width:32px;height:32px;background:#fff;border-radius:4px}
.copy{position:absolute;left:0;right:0;top:220px;border-top:1px solid rgba(255,255,255,.35);padding-top:12px;text-align:center;font-size:12px}
.copy small{position:absolute;right:22px;top:12px;font-size:10px}
</style>
</head>
<body>
<div class="abs page"></div>

<div class="abs logo"><span class="dot"></span>Southern Loop Ride</div>

<nav class="abs nav">
  <a class="home">Home</a>
  <a class="item">Journal</a>
  <a class="item">Riders</a>
  <a class="item">Supporters</a>
  <a class="item">Blog</a>
  <a class="item">Progress</a>
  <a class="item">Contact</a>
  <a class="donate">Get Donate</a>
</nav>

<div class="abs slider"><div class="photo" role="img" aria-label="Motorcyclist leaning into a coastal road curve at sunset"></div></div>
<div class="abs dots"><span></span><span class="on"></span><span></span></div>

<div class="abs band"></div>
<div class="abs video" role="img" aria-label="Video still of two riders on motorbikes seen from behind"></div>
<div class="abs play"><svg width="18" height="22" viewBox="0 0 18 22"><path d="M0 0L18 11L0 22Z" fill="#fff"/></svg></div>
<h2 class="abs welcome-title">Welcome! Southern Loop Ride</h2>
<p class="abs welcome-text">Accusantium doloremque laudantium, totam rem aperiam, eaque ipsa quae ab illo inventore veritatis et quasi architecto beatae vitae dicta sunt explicabo. Nemo enim ipsam voluptatem quia voluptas sit aspernatur aut odit aut fugit, sed quia consequuntur magni dolores eos qui ratione voluptatem sequi nesciunt. Neque porro quisquam est, qui dolorem ipsum quia dolor sit amet, consectetur, adipisci velit, sed quia non numquam eius modi tempora incidunt ut labore et dolore magnam aliquam quaerat voluptatem. Ut enim ad minima veniam, quis nostrum exercitationem ullam corporis suscipit laboriosam, nisi ut aliquid ex ea commodi consequatur? Quis autem vel eum iure reprehenderit</p>

<h2 class="abs h-section" style="left:120px;top:1114px">Our Blog</h2>

<div class="abs post-img one" role="img" aria-label="Motorbike parked on a country road at dusk"></div>
<h3 class="abs post-title" style="top:1428px;font-weight:400">Riverside Hall 2</h3>
<p class="abs post-date" style="top:1462px">Starting May 2014</p>
<p class="abs post-text" style="top:1490px">Riverside Hall 2 is a four story, 2.8 million square foot building located in Millbrook, Vic. Sam is responsible for the water distribution design and clash-free coordination of the main kitchen. The main kitchen supplies food for the entire campus and is the largest in the Yarra Valley.</p>
<div class="abs meta" style="top:1564px">
  <span class="ico"><svg width="12" height="11" viewBox="0 0 12 11"><path d="M0 4h3l6-4v11L3 7H0Z" fill="#3fb0a8"/></svg>Team members: <b>Sam Porter</b></span>
  <span class="ico"><svg width="12" height="10" viewBox="0 0 12 10"><ellipse cx="6" cy="4.5" rx="6" ry="4.5" fill="#3fb0a8"/></svg>15 comments</span>
  <span class="ico"><svg width="13" height="9" viewBox="0 0 13 9"><ellipse cx="6.5" cy="4.5" rx="6.5" ry="4.5" fill="#3fb0a8"/><circle cx="6.5" cy="4.5" r="2" fill="#fff"/></svg>15</span>
  <span class="share"><span></span><span></span><span></span><span></span></span>
</div>

<div class="abs post-img two" role="img" aria-label="Rider on a winding road through green tea hills"></div>
<h3 class="abs post-title" style="top:1887px;font-weight:400">The Harlow Centre for the Performing Arts</h3>
<p class="abs post-date" style="top:1921px">January 2009 – January 2010</p>
<p class="abs post-text" style="top:1950px">Riverside Hall 2 is a four story, 2.8 million square foot building located in Millbrook, Vic. Sam is responsible for the water distribution design and clash-free coordination of the main kitchen. The main kitchen supplies food for the entire campus and is the largest in the Yarra Valley.</p>
<div class="abs meta" style="top:2025px">
  <span class="ico"><svg width="12" height="11" viewBox="0 0 12 11"><path d="M0 4h3l6-4v11L3 7H0Z" fill="#3fb0a8"/></svg>Team members: <b>Sam Porter</b></span>
  <span class="ico"><svg width="12" height="10" viewBox="0 0 12 10"><ellipse cx="6" cy="4.5" rx="6" ry="4.5" fill="#3fb0a8"/></svg>15 comments</span>
  <span class="ico"><svg width="13" height="9" viewBox="0 0 13 9"><ellipse cx="6.5" cy="4.5" rx="6.5" ry="4.5" fill="#3fb0a8"/><circle cx="6.5" cy="4.5" r="2" fill="#fff"/></svg>15</span>
  <span class="share"><span></span><span></span><span></span><span></span></span>
</div>

<div class="abs pager"><span class="arr">«</span><span>1</span><span class="on">2</span><span>3</span><span>4</span><span>5</span><span>6</span><span class="arr">»</span></div>

<section class="abs don">
  <div class="don-head">Current Donations</div>
  <div class="don-row"><div>$85,000<small>Raised</small></div><div class="r">$68,000<small>Goal</small></div></div>
  <div class="bar"><i></i></div>
  <div class="don-stats"><div>$1.172<small>Raised</small></div><div>586<small>Donore</small></div><div>$5.250<small>Goal</small></div></div>
</section>

<section class="abs gps">
  <div class="gps-head">
    <div class="wd"><span></span><span></span><span></span></div>
    <div class="bat"><i></i></div>
    <svg class="wifi" width="14" height="12" viewBox="0 0 14 12"><path d="M7 12L0 4a10 10 0 0 1 14 0Z" fill="#fff"/></svg>
    <h3>GPS Tracker</h3>
    <p>Acticity Feed</p>
  </div>
  <div class="feed"><div class="avatar"></div><div><h4>Doloremque</h4><p>Accusantium doloremque laudantium</p></div></div>
  <div class="pace">
    <div>DIstance<strong>5.32<small> mi</small></strong></div>
    <div>Average Pace<strong>7:03</strong></div>
  </div>
  <div class="map" role="img" aria-label="Map of Australia with the riders' route marked"></div>
</section>

<h3 class="abs side-title">Bikes around Australia</h3>
<p class="abs side-text">Totam rem aperiam, eaque ipsa quae ab illo inventore veritatis et quasi architecto beatae vitae dicta sunt explicabo. Nemo enim ipsam voluptatem quia voluptas sit aspernatur aut odit aut fugit, sed quia consequuntur <a>www.harbourlight.org</a></p>
<p class="abs read">READ MORE</p>

<footer class="abs footer">
  <div class="f-col" style="left:24px;width:200px">
    <h5>Contact Us</h5>
    <p>Coastline Community Care<br>42 Wattle Grove Lane Tarrin,<br>NSW 2480</p>
    <div class="f-line"><svg width="16" height="16" viewBox="0 0 16 16"><path d="M3 1l3 3-2 2c1 2 4 5 6 6l2-2 3 3-2 2C7 15 1 9 1 3Z" fill="none" stroke="#fff" stroke-width="1.3"/></svg><span class="big">(02) 5550 1823</span></div>
    <div class="f-line"><svg width="16" height="12" viewBox="0 0 16 12"><rect x=".6" y=".6" width="14.8" height="10.8" fill="none" stroke="#fff" stroke-width="1.2"/><path d="M1 1l7 6 7-6" fill="none" stroke="#fff" stroke-width="1.2"/></svg><p>info@southernloop.org</p></div>
  </div>
  <div class="f-col" style="left:253px;width:240px">
    <h5>Latest Tweet`s</h5>
    <div style="display:flex;gap:14px"><span style="width:16px;height:16px;background:#fff;border-radius:2px;flex:none"></span>
    <p>Phasellus porta. Fusce susct varius mi. Cum sociis natoque penabus et magnis dis parturient montes, nascetur ridiculus mus. See more here http://sl.link/a7Kq2</p></div>
  </div>
  <div class="f-col" style="left:535px;width:260px">
    <h5>Newsletter</h5>
    <p>Excepteur sint occaecat cupidatat non proident, sunt in culpa qui officia deserunt mollit anim</p>
    <div class="news"><span>Enter your email address</span><b>Sign Up</b></div>
  </div>
  <div class="f-col" style="left:840px">
    <h5>Social Media</h5>
    <div class="soc"><span></span><span></span><span></span></div>
  </div>
  <div class="copy">2016 All Rights Reserved.<small>C 19</small></div>
</footer>
</body>
</html>
```